Social Media App Needs PPT Template

We need a PowerPoint template for a new social media company based in the DC area called "Bold Ledger." We provide an interactive digital platform for executives to share actionable advice. We would like to see designs that use our orange logo color as an accent, but are mainly grey, white, and black. The final design should communicate clean, chic, modern, and professional.

Target Market(s)

Executives

Industry/Entity Type

Information Technology

Font styles to use
Sans Serif

Colors
f78f20
fbe7d2
ffffff
000000
e8e8e8
757575

Requirements
Must have
• My project must have title page and many options for the body of the ppt (graphs, tables, etc). It also needs to be easy to modify. I must have someone who is experienced in creating powerpoint templates.
Nice to have
• It would be nice to have a very modern and clean design that includes the logo on every page, but still leaves a lot of room for the content of the slide
Should not have
• My design project should not look to busy.

```html
<!DOCTYPE html>
<html lang="en">
<head>
<meta charset="utf-8">
<title>Bold Ledger – About Our Company</title>
<link href="https://fonts.googleapis.com/css2?family=Lato:wght@300;400;700&display=swap" rel="stylesheet">
<style>
  :root {
    --orange: #f78f20;
    --orange-deep: #e8821b;
    --charcoal: #444444;
    --ink: #3a3a3a;
    --text: #4a4a4a;
    --muted: #757575;
    --rule: #2f3440;
    --paper: #f7f7f7;
    --backdrop: #939393;
    --white: #ffffff;
  }
  * { margin: 0; padding: 0; box-sizing: border-box; }
  html, body {
    width: 1200px; height: 960px; overflow: hidden;
    background: var(--backdrop);
    font-family: "Lato", sans-serif;
  }
  .page-label {
    position: absolute; top: 44px; left: 0; width: 1200px;
    text-align: center; color: var(--white);
    font-weight: 300; font-size: 24px;
  }
  .slide {
    position: absolute; left: 87px; top: 128px;
    width: 1046px; height: 784px;
    background: radial-gradient(ellipse at 50% 40%, #ffffff 0%, var(--paper) 60%, #efefef 100%);
    overflow: hidden;
  }
  .header-art, .footer-art { position: absolute; left: 0; }
  .header-art { top: 0; }
  .footer-art { top: 742px; }
  .slide-title {
    position: absolute; left: 32px; top: 66px;
    color: var(--white); font-weight: 300; font-size: 38px;
    letter-spacing: 0.2px;
  }
  .brand {
    position: absolute; left: 846px; top: 74px;
    display: flex; align-items: center; gap: 9px;
    color: var(--white); font-weight: 700; font-size: 22px;
  }
  .brand-dot {
    width: 18px; height: 18px; border-radius: 50%;
    background: var(--orange);
  }
  .team {
    position: absolute; top: 222px; left: 0; width: 100%;
  }
  .member { position: absolute; width: 284px; }
  .member:nth-child(1) { left: 35px; }
  .member:nth-child(2) { left: 374px; }
  .member:nth-child(3) { left: 715px; }
  .portrait {
    width: 284px; height: 172px;
    border: 1.5px solid var(--orange);
  }
  .portrait.office { background: linear-gradient(100deg, #e9edf1 0%, #cfd6de 45%, #eef1f3 100%); }
  .portrait.city { background: linear-gradient(180deg, #d6e8f2 0%, #bcd2df 55%, #2d2f36 100%); }
  .portrait.garden { background: linear-gradient(120deg, #6f7d3e 0%, #9aa25a 40%, #b8b6a8 70%, #7d8a4a 100%); }
  .member-name {
    margin-top: 18px; color: var(--ink);
    font-weight: 700; font-size: 22px; line-height: 1.2;
  }
  .member-role {
    margin-top: 2px; margin-left: -1px; color: var(--muted);
    font-weight: 400; font-size: 16px;
  }
  .rule { height: 2px; background: var(--rule); }
  .rule.top { margin-top: 12px; }
  .member-bio {
    margin-top: 20px; margin-left: -2px; width: 288px;
    color: var(--text); font-size: 15px; line-height: 19.2px;
    text-align: justify;
  }
  .rule.bottom { position: absolute; top: 434px; left: 0; width: 284px; }
  .footer-text {
    position: absolute; left: 28px; top: 748px;
    color: var(--white); font-size: 14px; font-weight: 400;
  }
  .footer-text .sep { margin: 0 8px; }
</style>
</head>
<body>
  <div class="page-label">Page 10</div>

  <section class="slide">
    <svg class="header-art" width="1046" height="150" viewBox="0 0 1046 150" aria-hidden="true">
      <polygon points="0,49 793,49 709,130 0,130" fill="var(--orange-deep)"/>
      <polygon points="560,49 793,49 740,100 640,100" fill="var(--orange)" opacity="0.55"/>
      <polygon points="580,108 731,108 709,130 566,130" fill="var(--orange)" opacity="0.45"/>
      <polygon points="801,49 1046,49 1046,130 717,130" fill="var(--charcoal)"/>
      <polygon points="815,34 1046,34 1046,44 805,44" fill="var(--orange)"/>
      <polygon points="0,135 703,135 693,145 0,145" fill="var(--charcoal)"/>
    </svg>
    <h1 class="slide-title">About Our Company</h1>
    <div class="brand"><span class="brand-dot"></span>Bold Ledger</div>

    <div class="team">
      <article class="member">
        <div class="portrait office" role="img" aria-label="Portrait photo of a smiling executive in an office"></div>
        <h2 class="member-name">Mr D. Smilth</h2>
        <p class="member-role">(President)</p>
        <div class="rule top"></div>
        <p class="member-bio">Lorem ipsum dolor sit amet, consectetuer adipiscing elit, sed diam nonummy nibh euismod tincidunt ut laoreet dolore magna aliquam erat volutpat. Ut wisi enim ad minim veniam, quis nostrud exerci tation ullamcorper suscipit lobortis nisl ut aliquip ex ea commodo consequat.</p>
        <div class="rule bottom"></div>
      </article>
      <article class="member">
        <div class="portrait city" role="img" aria-label="Portrait photo of an executive in a dark suit outdoors"></div>
        <h2 class="member-name">Mr D. Smilth</h2>
        <p class="member-role">(President)</p>
        <div class="rule top"></div>
        <p class="member-bio">Lorem ipsum dolor sit amet, consectetuer adipiscing elit, sed diam nonummy nibh euismod tincidunt ut laoreet dolore magna aliquam erat volutpat. Ut wisi enim ad minim veniam, quis nostrud exerci tation ullamcorper suscipit lobortis nisl ut aliquip ex ea commodo consequat.</p>
        <div class="rule bottom"></div>
      </article>
      <article class="member">
        <div class="portrait garden" role="img" aria-label="Portrait photo of an executive in a grey suit in a park"></div>
        <h2 class="member-name">Mr D. Smilth</h2>
        <p class="member-role">(President)</p>
        <div class="rule top"></div>
        <p class="member-bio">Lorem ipsum dolor sit amet, consectetuer adipiscing elit, sed diam nonummy nibh euismod tincidunt ut laoreet dolore magna aliquam erat volutpat. Ut wisi enim ad minim veniam, quis nostrud exerci tation ullamcorper suscipit lobortis nisl ut aliquip ex ea commodo consequat.</p>
        <div class="rule bottom"></div>
      </article>
    </div>

    <svg class="footer-art" width="1046" height="42" viewBox="0 0 1046 42" aria-hidden="true">
      <polygon points="0,0 298,0 267,31 0,31" fill="var(--charcoal)"/>
      <polygon points="304,0 1046,0 1046,31 273,31" fill="var(--orange-deep)"/>
    </svg>
    <p class="footer-text">www.boldledger.com<span class="sep">|</span>Page 8</p>
  </section>
</body>
</html>
```